Pavecrest Works

Im looking for something similar to (tarvalepaving.com) web site. I really want it to pop!
services we offer:
- Seal Coating
- Crack Filling
- Striping
- Asphalt
- Concrete
- Signage
- Road Grinding
- Grading
- Hydro Blasting
- Recycled asphalt
- Dumpster Pads
- Pressure Washing
- Wheel blocks
- Bollard installation
- Commercial Curbing
- Job site clean up
- Sweeping
- Forestry Clean up
- ADA Compliant work
- Speed bump installation and removal
- Snow removal
- Custom stair sets (Commercial)
Target Market(s)
Parking lot maintenance, asphalt repairs, road grading
Industry/Entity Type
construction, parking lot maintenance
Number of Pages Required
2 page

```html
<!DOCTYPE html>
<html lang="en">
<head>
<meta charset="utf-8">
<title>Pavecrest Works</title>
<link href="https://fonts.googleapis.com/css2?family=Oswald:wght@500;600&family=Roboto:ital,wght@0,400;0,500;0,700;1,400&display=swap" rel="stylesheet">
<style>
:root{
  --green:#52f00f;
  --ink:#111111;
  --text:#444444;
  --muted:#666666;
  --light:#f4f4f4;
  --white:#ffffff;
  --red:#c0392b;
  --footer:#111111;
}
*{box-sizing:border-box;margin:0;padding:0}
html,body{width:1200px;height:4713px;overflow:hidden}
body{font-family:'Roboto',sans-serif;color:var(--ink);background:var(--white);position:relative}
.heading{font-family:'Oswald',sans-serif;font-weight:500;text-transform:uppercase;letter-spacing:0}
.btn{position:absolute;background:var(--green);color:var(--ink);font-weight:700;font-size:15px;text-transform:uppercase;border-radius:30px;display:flex;align-items:center;justify-content:center}
.ph{position:absolute}

/* header */
.site-header{position:absolute;left:0;top:0;width:1200px;height:93px;background:var(--white)}
.brand{position:absolute;left:117px;top:18px;display:flex;align-items:center;gap:12px;font-family:'Roboto',sans-serif;font-weight:700;font-size:30px;color:var(--ink);letter-spacing:1px;text-transform:uppercase;white-space:nowrap}
.brand-dot{width:14px;height:14px;background:var(--ink);flex:none}
.phone-pill{position:absolute;left:731px;top:10px;display:flex;align-items:center;gap:10px;font-size:16px;font-weight:500}
.phone-pill .ico{width:34px;height:34px;border-radius:50%;background:var(--green);display:flex;align-items:center;justify-content:center}
.quote-btn{left:934px;top:9px;width:154px;height:38px;font-size:15px}
.main-nav{position:absolute;right:112px;top:60px;display:flex;gap:38px;font-size:15px;font-weight:500;text-transform:uppercase}
.main-nav .active{color:var(--red)}

/* hero */
.hero{position:absolute;left:0;top:93px;width:1200px;height:619px;background:linear-gradient(180deg,#b9c6d3 0%,#8d97a0 30%,#3b3d40 60%,#2a2b2d 100%)}
.hero-machine{position:absolute;left:180px;top:0;width:520px;height:560px;background:radial-gradient(ellipse at 50% 55%,#d59b1c 0%,#a87516 45%,rgba(60,50,30,0) 72%)}
.hero-title{position:absolute;left:691px;top:160px;font-size:92px;color:var(--white);line-height:1}
.hero-sub{position:absolute;left:694px;top:270px;width:400px;font-size:20px;line-height:33px;color:var(--white)}
.hero-cta{left:695px;top:353px;width:172px;height:51px}
.hero-arrow{position:absolute;top:290px}
.dots{position:absolute;left:563px;top:580px;display:flex;gap:10px}
.dots span{width:10px;height:10px;border-radius:50%;background:rgba(255,255,255,.5)}
.dots .on{background:var(--white)}

/* about */
.about{position:absolute;left:0;top:712px;width:1200px;height:854px}
.eyebrow{position:absolute;left:112px;top:66px;font-size:14px;font-weight:700;text-transform:uppercase;display:flex;align-items:center;gap:10px}
.eyebrow i{display:block;width:46px;height:3px;background:var(--ink)}
.about-title{position:absolute;left:110px;top:86px;font-size:50px;line-height:1.1;white-space:nowrap}
.about-copy{position:absolute;left:655px;top:62px;width:430px;font-size:14px;line-height:25px;color:var(--text)}
.about-copy p+p{margin-top:12px}
.about-cta{left:655px;top:283px;width:172px;height:49px;z-index:2}

/* services */
.services{position:absolute;left:0;top:1566px;width:1200px;height:607px;background:var(--light)}
.section-title{position:absolute;left:0;width:1200px;text-align:center;font-size:44px;line-height:1}
.service-card{position:absolute;top:144px;width:314px;height:379px;background:var(--white);border:1px solid #e2e2e2;text-align:center}
.service-card .ph{left:0;top:0;width:312px;height:205px}
.service-card h3{position:absolute;left:0;top:224px;width:100%;font-size:25px;font-weight:500;text-transform:uppercase;letter-spacing:.5px}
.service-card p{position:absolute;left:16px;top:260px;width:280px;font-size:13px;line-height:25px;color:var(--muted)}
.service-card a{position:absolute;left:0;top:340px;width:100%;font-size:13px;font-weight:700;color:var(--ink);text-decoration:underline;text-transform:uppercase}
.side-arrow{position:absolute}

/* testimonials */
.testimonials{position:absolute;left:0;top:2173px;width:1200px;height:664px;background:linear-gradient(135deg,#3a3a32 0%,#2b2b26 45%,#4a3d1a 80%,#2a2519 100%)}
.testimonials .section-title{color:var(--white);top:104px}
.testimonials .lead{position:absolute;left:0;top:160px;width:1200px;text-align:center;font-size:20px;color:var(--white)}
.t-card-back{position:absolute;left:214px;top:256px;width:772px;height:307px;background:rgba(255,255,255,.9);border-radius:6px}
.t-card{position:absolute;left:236px;top:238px;width:728px;height:342px;background:var(--white);border-radius:6px;text-align:center}
.quote-badge{position:absolute;left:328px;top:-20px;width:72px;height:72px;border-radius:50%;background:var(--green);display:flex;align-items:center;justify-content:center}
.t-card blockquote{position:absolute;left:40px;top:66px;width:648px;font-size:20px;font-style:italic;line-height:33px;color:var(--text)}
.t-card .name{position:absolute;left:0;top:222px;width:100%;font-size:20px;font-weight:500;text-transform:uppercase}
.t-card .role{position:absolute;left:0;top:250px;width:100%;font-size:14px;color:var(--muted)}
.t-card .stars{position:absolute;left:0;top:270px;width:100%;font-size:20px;color:#f5c518;letter-spacing:1px}

/* gallery */
.gallery{position:absolute;left:0;top:2837px;width:1200px;height:918px;background:var(--white)}
.gallery .section-title{top:90px}

/* contact */
.contact{position:absolute;left:0;top:3755px;width:1200px;height:576px;background:linear-gradient(180deg,#2c2c2a 0%,#3a3a2c 50%,#2f2a1e 100%)}
.contact .section-title{color:var(--white);top:98px}
.field{position:absolute;background:var(--white);font-size:15px;color:#555;padding:16px 12px}
.submit{left:503px;top:437px;width:194px;height:52px}

/* footer */
.site-footer{position:absolute;left:0;top:4331px;width:1200px;height:382px;background:var(--footer);color:var(--white)}
.foot-brand{position:absolute;left:112px;top:92px;width:240px;display:flex;align-items:center;gap:12px;font-weight:700;font-size:28px;line-height:32px;text-transform:uppercase;letter-spacing:1px}
.foot-brand .brand-dot{background:var(--white)}
.socials{position:absolute;left:131px;top:203px;display:flex;gap:14px}
.socials span{width:30px;height:30px;border-radius:50%}
.foot-col h4{position:absolute;top:76px;font-size:17px;font-weight:500;text-transform:uppercase;letter-spacing:.5px;white-space:nowrap}
.foot-col h4::after{content:"";position:absolute;left:0;top:32px;width:36px;height:2px;background:var(--white)}
.quick-links{position:absolute;left:404px;top:122px;list-style:none;font-size:14px;line-height:26.8px}
.contact-item{position:absolute;left:571px;display:flex;gap:12px;font-size:14px;line-height:22px;align-items:flex-start}
.contact-item .ico{flex:none;width:34px;height:34px;border-radius:50%;background:var(--green);display:flex;align-items:center;justify-content:center}
.map{position:absolute;left:880px;top:118px;width:208px;height:150px;background:#eef0f2}
.copyright{position:absolute;left:0;top:338px;width:1200px;text-align:center;font-size:14px}
</style>
</head>
<body>

<header class="site-header">
  <div class="brand"><span class="brand-dot"></span>Pavecrest Works</div>
  <div class="phone-pill"><span class="ico"><svg width="16" height="16" viewBox="0 0 24 24"><path d="M6.6 10.8a15 15 0 006.6 6.6l2.2-2.2a1 1 0 011-.25 11.4 11.4 0 003.6.57 1 1 0 011 1V20a1 1 0 01-1 1A17 17 0 013 4a1 1 0 011-1h3.5a1 1 0 011 1 11.4 11.4 0 00.57 3.6 1 1 0 01-.25 1z" fill="#111"/></svg></span>888 - 888 - 8888</div>
  <div class="btn quote-btn">Get a Quote</div>
  <nav class="main-nav"><span class="active">Home</span><span>About</span><span>Services</span><span>Testimonials</span><span>Gallery</span><span>Contact</span></nav>
</header>

<section class="hero">
  <div class="hero-machine" role="img" aria-label="Yellow asphalt roller on a freshly paved lot"></div>
  <h1 class="heading hero-title">Pavecrest</h1>
  <p class="hero-sub">Lorem ipsum dolor sit amettetur adipiscing elit, sed do eiusmod mpor incididunt</p>
  <div class="btn hero-cta">Get Started</div>
  <svg class="hero-arrow" style="left:76px" width="20" height="36" viewBox="0 0 20 36"><path d="M18 2L2 18l16 16" stroke="#fff" stroke-width="2" fill="none"/></svg>
  <svg class="hero-arrow" style="left:1106px" width="20" height="36" viewBox="0 0 20 36"><path d="M2 2l16 16L2 34" stroke="#fff" stroke-width="2" fill="none"/></svg>
  <div class="dots"><span></span><span class="on"></span><span></span><span></span></div>
</section>

<section class="about">
  <div class="eyebrow">About Us <i></i></div>
  <h2 class="heading about-title">Pavecrest Works</h2>
  <div class="ph" style="left:112px;top:171px;width:450px;height:461px;background:linear-gradient(180deg,#cfe0ea 0%,#3d5a2a 35%,#4a6b2f 65%,#6b6b62 100%)" role="img" aria-label="Paved path through a pine forest"></div>
  <div class="about-copy">
    <p>Lorem ipsum dolor sit amet, consectetur adipiscinged do eiusmod tempor incididunt ut labore et dolore ua. Quis ipsum suspendisse ultrices gravida. Risus commodo viverra maecenas accumsan lacus vel facilisis.</p>
    <p>Lorem ipsum dolor sit amet, consectetur adig elit, sed do eiusmod tempor incididunt ut labore eagna aliqua. Quis ipsum suspendisse ultrices gravida. Risus commodo</p>
  </div>
  <div class="btn about-cta">Learn More</div>
  <div class="ph" style="left:629px;top:301px;width:459px;height:463px;background:linear-gradient(180deg,#5f7a45 0%,#4a4a46 45%,#8b8677 75%,#a39e90 100%)" role="img" aria-label="Skid steer grading gravel along a roadside"></div>
</section>

<section class="services">
  <h2 class="heading section-title" style="top:60px">Our Services</h2>
  <svg class="side-arrow" style="left:78px;top:340px" width="14" height="28" viewBox="0 0 14 28"><path d="M13 1L1 14l12 13" stroke="#333" stroke-width="2" fill="none"/></svg>
  <svg class="side-arrow" style="left:1108px;top:340px" width="14" height="28" viewBox="0 0 14 28"><path d="M1 1l12 13L1 27" stroke="#333" stroke-width="2" fill="none"/></svg>
  <article class="service-card" style="left:112px">
    <div class="ph" style="background:linear-gradient(180deg,#9cb1c4 0%,#7a6a48 45%,#8a7a5c 100%)" role="img" aria-label="Skid steer applying seal coat"></div>
    <h3>Seal Coating</h3>
    <p>Sed ut perspiciatunde omnis iste natus error sit voluptatsantium doloremque laudantium, totam rem aperiam, eaque ipsa</p>
    <a>Learn More »</a>
  </article>
  <article class="service-card" style="left:444px">
    <div class="ph" style="background:linear-gradient(180deg,#8e8b84 0%,#6f6c66 60%,#3a3835 100%)" role="img" aria-label="Crack filling on asphalt"></div>
    <h3>Crack Filling</h3>
    <p>Sed ut perspiciatunde omnis iste natus error sit voluptatsantium doloremque laudantium, totam rem aperiam, eaque ipsa</p>
    <a>Learn More »</a>
  </article>
  <article class="service-card" style="left:776px">
    <div class="ph" style="background:linear-gradient(180deg,#7e8086 0%,#55575c 55%,#6a6c71 100%)" role="img" aria-label="Line striping machine on a parking lot"></div>
    <h3>Striping</h3>
    <p>Sed ut perspiciatunde omnis iste natus error sit voluptatsantium doloremque laudantium, totam rem aperiam, eaque ipsa</p>
    <a>Learn More »</a>
  </article>
</section>

<section class="testimonials" role="img" aria-label="Dark background of a tracked machine on a dirt site">
  <h2 class="heading section-title">What Our Customers Are Saying</h2>
  <p class="lead">Lorem ipsum dolor sit amet, consectetur adipiscing</p>
  <div class="t-card-back"></div>
  <div class="t-card">
    <div class="quote-badge"><svg width="34" height="28" viewBox="0 0 34 28"><path d="M2 26V14C2 7 6 3 13 2v5c-4 1-5 3-5 7h5v12zM20 26V14c0-7 4-11 11-12v5c-4 1-5 3-5 7h5v12z" fill="#111"/></svg></div>
    <blockquote>Lorem ipsum dolor sit amet, consectetur adipiscing elit,d do eiusmod tempor incididunt ut labore et dolore magna aliqua. Qsum suspendisse ultrmodo viverra maecenas accumsan lacus vel facilisis. Lorem ipsum dolor sit amet, consectetur adipiscing elit</blockquote>
    <div class="name">- John Smith</div>
    <div class="role">Finibus Bonorum et Malorum</div>
    <div class="stars">★★★★★</div>
  </div>
  <svg class="side-arrow" style="left:173px;top:388px" width="16" height="26" viewBox="0 0 16 26"><path d="M14 2L3 13l11 11" stroke="#fff" stroke-width="3" fill="none"/></svg>
  <svg class="side-arrow" style="left:1003px;top:388px" width="16" height="26" viewBox="0 0 16 26"><path d="M2 2l11 11L2 24" stroke="#fff" stroke-width="3" fill="none"/></svg>
</section>

<section class="gallery">
  <h2 class="heading section-title">Our Gallery</h2>
  <div class="ph" style="left:112px;top:159px;width:316px;height:326px;background:linear-gradient(180deg,#8c8680 0%,#9a968f 50%,#c9b340 70%,#8f8b84 100%)" role="img" aria-label="ADA tactile pad in new concrete"></div>
  <div class="ph" style="left:443px;top:159px;width:316px;height:326px;background:linear-gradient(180deg,#e4e4e2 0%,#cfcfcd 45%,#8e8b86 75%,#a8a49d 100%)" role="img" aria-label="Concrete entry slab by a building"></div>
  <div class="ph" style="left:774px;top:159px;width:316px;height:326px;background:linear-gradient(180deg,#c7c9ca 0%,#4a5a60 40%,#2f3437 100%)" role="img" aria-label="Roller paving under a parking structure"></div>
  <div class="ph" style="left:112px;top:496px;width:316px;height:326px;background:linear-gradient(180deg,#9fb2c3 0%,#6f7568 25%,#9a3a2e 55%,#a9443a 100%)" role="img" aria-label="Red stamped asphalt crosswalk"></div>
  <div class="ph" style="left:443px;top:496px;width:316px;height:326px;background:linear-gradient(180deg,#6d6a4e 0%,#5b5943 45%,#bfa32a 65%,#6d6b66 100%)" role="img" aria-label="Yellow bollards at a utility room"></div>
  <div class="ph" style="left:774px;top:496px;width:316px;height:326px;background:linear-gradient(180deg,#a7b7c6 0%,#5f6360 30%,#a3483c 60%,#b24f42 100%)" role="img" aria-label="Red brick-pattern crosswalk on a road"></div>
</section>

<section class="contact" role="img" aria-label="Dark background of equipment by a cornfield">
  <h2 class="heading section-title">Get In Touch</h2>
  <div class="field" style="left:205px;top:178px;width:386px;height:49px">First Name</div>
  <div class="field" style="left:605px;top:178px;width:388px;height:49px">Last Name</div>
  <div class="field" style="left:205px;top:245px;width:386px;height:50px">Email</div>
  <div class="field" style="left:605px;top:245px;width:388px;height:50px">Phone</div>
  <div class="field" style="left:205px;top:313px;width:788px;height:106px">How Can We Help?</div>
  <div class="btn submit">Submit</div>
</section>

<footer class="site-footer">
  <div class="foot-brand"><span class="brand-dot"></span><span>Pavecrest<br>Works</span></div>
  <div class="socials" aria-label="Social links"><span style="background:#3b5998"></span><span style="background:#d6249f"></span><span style="background:#0a66c2"></span><span style="background:#1f5fbf"></span></div>
  <div class="foot-col"><h4 style="left:404px">Quick Links</h4></div>
  <ul class="quick-links"><li>Home</li><li>About</li><li>Services</li><li>Testimonials</li><li>Gallery</li><li>Contact</li></ul>
  <div class="foot-col"><h4 style="left:571px">Contact Details</h4></div>
  <div class="contact-item" style="top:124px"><span class="ico"><svg width="14" height="18" viewBox="0 0 14 18"><path d="M7 0a7 7 0 00-7 7c0 5 7 11 7 11s7-6 7-11a7 7 0 00-7-7zm0 9.5A2.5 2.5 0 117 4.5a2.5 2.5 0 010 5z" fill="#111"/></svg></span><span>123 Your Adress Goes Here.<br>CA, 1234567</span></div>
  <div class="contact-item" style="top:188px;align-items:center"><span class="ico"><svg width="16" height="16" viewBox="0 0 24 24"><path d="M6.6 10.8a15 15 0 006.6 6.6l2.2-2.2a1 1 0 011-.25 11.4 11.4 0 003.6.57 1 1 0 011 1V20a1 1 0 01-1 1A17 17 0 013 4a1 1 0 011-1h3.5a1 1 0 011 1 11.4 11.4 0 00.57 3.6 1 1 0 01-.25 1z" fill="#111"/></svg></span><span>888-888-8888</span></div>
  <div class="contact-item" style="top:241px;align-items:center"><span class="ico"><svg width="16" height="12" viewBox="0 0 16 12"><rect x="0" y="0" width="16" height="12" rx="1" fill="#111"/><path d="M1 1l7 6 7-6" stroke="#52f00f" stroke-width="1.5" fill="none"/></svg></span><span>info@pavecrestworks.com</span></div>
  <div class="foot-col"><h4 style="left:880px">Location Map</h4></div>
  <div class="map" role="img" aria-label="Street map showing the office location"></div>
  <p class="copyright">© 2021 Pavecrest Works.All Rights Reserved</p>
</footer>

</body>
</html>
```